professional business card design for technology company

We are a small technology consulting firm, specialising in consulting based around Cloud and Managed services. Our colour scheme is yellow, blue and white, as you can see in the logos. Although we are based in melbourne australia, due to the nature of our work, our clients can be located anywhere. We are looking for a clean, professional, positive look - similar to our company logo

Target Market(s)

small business

Industry/Entity Type

Business

Contact Information for Business Card

eye catching, designed to incorporate some level of raised printing. Must contain website address, phone number, name and job title

Requirements
Must have
• Logo (attached) - use of the same colour scheme

```html
<!DOCTYPE html>
<html lang="en">
<head>
<meta charset="utf-8">
<title>Nuvaline Business Card</title>
<link href="https://fonts.googleapis.com/css2?family=Open+Sans:wght@400;600;700&display=swap" rel="stylesheet">
<style>
  :root {
    --backdrop: #b9bec6;
    --card-light: #ffffff;
    --card-shade: #e3e4e6;
    --ink-grey: #505052;
    --panel-grey: #606062;
    --sky-blue: #39a9e1;
    --sun-yellow: #f6d21c;
    --white: #ffffff;
  }
  * { margin: 0; padding: 0; box-sizing: border-box; }
  html, body {
    width: 1200px; height: 865px; overflow: hidden;
    background: var(--backdrop);
    font-family: "Open Sans", Arial, sans-serif;
  }
  .canvas { position: relative; width: 1200px; height: 865px; }
  .card {
    position: absolute; width: 520px; height: 300px; overflow: hidden;
    background: radial-gradient(ellipse at 55% 45%, var(--card-light) 0%, var(--card-shade) 100%);
    box-shadow: 0 6px 18px rgba(0,0,0,0.18);
  }
  .card-front { left: 70px; top: 110px; }
  .card-back { left: 610px; top: 455px; }

  .brand {
    display: flex; align-items: center; gap: 14px;
    color: var(--ink-grey); font-weight: 700; letter-spacing: -1px;
  }
  .brand-dot { border-radius: 50%; background: var(--sky-blue); flex: none; }
  .card-front .brand {
    position: absolute; left: 0; right: 0; top: 0; bottom: 0;
    justify-content: center; font-size: 64px;
  }
  .card-front .brand-dot { width: 54px; height: 54px; }

  .card-back .swoosh { position: absolute; inset: 0; }
  .card-back .brand { position: absolute; left: 36px; top: 96px; font-size: 40px; gap: 10px; }
  .card-back .brand-dot { width: 34px; height: 34px; }
  .holder { position: absolute; left: 38px; top: 160px; }
  .holder-name { color: var(--sky-blue); font-weight: 700; font-size: 16px; }
  .holder-title { color: #333; font-size: 15px; margin-top: 2px; }

  .contact {
    position: absolute; right: 22px; top: 104px;
    list-style: none; text-align: right;
    color: var(--white); font-size: 11.5px; line-height: 17px;
  }
  .contact svg { width: 10px; height: 10px; vertical-align: -1px; margin-left: 4px; fill: var(--white); }
</style>
</head>
<body>
<main class="canvas">

  <section class="card card-front" aria-label="Card front">
    <div class="brand"><span class="brand-dot"></span><span class="brand-name">Nuvaline</span></div>
  </section>

  <section class="card card-back" aria-label="Card back">
    <svg class="swoosh" viewBox="0 0 520 300" aria-hidden="true">
      <path d="M520 0 L408 0 C368 120 300 230 110 268 L70 300 L520 300 Z" fill="var(--panel-grey)"/>
      <path d="M395 0 C352 118 290 222 104 262 L60 300 L70 300 L110 268 C300 230 368 120 408 0 Z" fill="var(--white)"/>
      <path d="M388 4 C340 120 270 215 40 252 L18 262 C250 240 335 140 378 30 C355 150 270 212 160 244 C290 222 360 140 388 4 Z" fill="var(--sky-blue)"/>
      <path d="M384 10 C330 140 250 205 100 226 C260 214 345 150 384 10 Z" fill="var(--sky-blue)"/>
    </svg>

    <div class="brand"><span class="brand-dot"></span><span class="brand-name">Nuvaline</span></div>

    <div class="holder">
      <p class="holder-name">Marlo Quinn-Adair</p>
      <p class="holder-title">Consultant</p>
    </div>

    <ul class="contact">
      <li>Level 12, 40 Harbour</li>
      <li>Lane Docklands<svg viewBox="0 0 10 10"><path d="M2 0h2l1 3-1.5 1a6 6 0 0 0 2.5 2.5L7 5l3 1v2c0 1-1 2-2 2A8 8 0 0 1 0 2c0-1 1-2 2-2z"/></svg></li>
      <li>03 9000 4821<svg viewBox="0 0 10 10"><rect x="1" y="3" width="8" height="7"/><rect x="3" y="0" width="4" height="3"/></svg></li>
      <li>03 9000 4821<svg viewBox="0 0 10 10"><path d="M0 2h10v7H0z"/></svg></li>
      <li>hello@nuvaline.io</li>
      <li>www.nuvaline.io</li>
    </ul>
  </section>

</main>
</body>
</html>
```